Hollow Thicket, a 3d voxel survival video game needs a card for gaming conventions

I am the lead developer for Hollow Thicket http://www.HollowThicket.example and need a business card to hand out at an indie gaming convention
The card would need to include the game name, website url, my name, position (Lead Developer), e-mail and phone number
The game is a 3d, voxel (with smooth terrain) based survival game with guns and wildlife. The main icon of the game would likely be a grizzly bear but I am willing to accept other designs too.
Attached is a media kit for the game with some images you can use but don't have to its just what little art I can provide. Anything on the website or from the video game can also be used. unrelated art can also be used.
Target Market(s)
Indie Developers/publishers at conferences
Industry/Entity Type
Games
Contact Information for Business Card
Name: Corin Waldrick
Position: Lead Developer
E-mail: Pale_Kettle@mailbox.example
Phone number: 555-372-1186

```html
<!DOCTYPE html>
<html lang="en">
<head>
<meta charset="utf-8">
<title>Hollow Thicket – Business Card</title>
<link rel="stylesheet" href="https://fonts.googleapis.com/css2?family=Open+Sans:wght@400;600;800&display=swap">
<style>
  :root {
    --page: #e9e6df;
    --sky-top: #4a86c6;
    --sky-low: #a9c6de;
    --lake: #4f79a8;
    --lake-deep: #3f6390;
    --panel: rgba(236, 238, 236, 0.9);
    --ink: #1e1e1e;
    --brand-red: #b52a1f;
    --back-light: #cfcbb4;
    --back-mid: #6f6c48;
    --back-dark: #1f1e12;
    --fur-light: #8a5a34;
    --fur-dark: #5e3a20;
  }
  * { box-sizing: border-box; margin: 0; padding: 0; }
  html, body { width: 1200px; height: 780px; overflow: hidden; }
  body {
    background: var(--page);
    font-family: "Open Sans", Arial, sans-serif;
    color: var(--ink);
    position: relative;
  }
  .card {
    position: absolute;
    top: 235px;
    width: 540px;
    height: 310px;
    overflow: hidden;
    border-radius: 3px;
    box-shadow: 0 6px 18px rgba(0,0,0,0.25);
  }
  .card--front { left: 40px; }
  .card--back { left: 620px; }

  .front__scene {
    position: absolute; inset: 0;
    background: linear-gradient(180deg, var(--sky-top) 0%, var(--sky-low) 40%, var(--lake) 62%, var(--lake-deep) 100%);
  }
  .front__panel {
    position: absolute;
    top: 24px; right: 0;
    width: 290px;
    background: var(--panel);
    padding: 20px 22px 22px;
  }
  .brand-name {
    font-weight: 800;
    font-size: 24px;
    letter-spacing: 0.5px;
    text-transform: uppercase;
    color: var(--brand-red);
    line-height: 1.1;
    white-space: nowrap;
  }
  .person { margin-top: 14px; }
  .person__name { font-size: 20px; font-weight: 600; line-height: 1.15; }
  .person__role { font-size: 14px; line-height: 1.25; }
  .contacts { list-style: none; margin-top: 12px; font-size: 11.5px; line-height: 1.65; }
  .contacts li { display: flex; align-items: center; gap: 7px; white-space: nowrap; }
  .contacts svg { width: 11px; height: 11px; flex: none; }

  .back__field {
    position: absolute; inset: 0;
    background: radial-gradient(ellipse 60% 65% at 50% 50%, var(--back-light) 0%, var(--back-mid) 55%, var(--back-dark) 100%);
  }
  .back__photo {
    position: absolute;
    left: 190px; top: 50px;
    width: 160px; height: 90px;
    border-radius: 4px;
    background: linear-gradient(135deg, var(--fur-light) 0%, var(--fur-dark) 100%);
  }
  .back__name {
    position: absolute;
    left: 0; right: 0; top: 160px;
    text-align: center;
    font-weight: 800;
    font-size: 44px;
    line-height: 1.1;
    letter-spacing: 2px;
    text-transform: uppercase;
    color: var(--brand-red);
    white-space: nowrap;
  }
</style>
</head>
<body>
  <section class="card card--front">
    <div class="front__scene" role="img" aria-label="Photo of a grizzly bear sitting on a rock by a mountain lake with cliffs, trees and blue sky"></div>
    <div class="front__panel">
      <div class="brand-name">Hollow Thicket</div>
      <div class="person">
        <div class="person__name">Corin Waldrick</div>
        <div class="person__role">Lead Developer</div>
      </div>
      <ul class="contacts">
        <li>
          <svg viewBox="0 0 12 12" aria-hidden="true"><path d="M2 1h3l1 3-2 1a7 7 0 0 0 3 3l1-2 3 1v3c-6 0-10-4-9-9z" fill="#222"/></svg>
          555-372-1186
        </li>
        <li>
          <svg viewBox="0 0 12 12" aria-hidden="true"><rect x="0.5" y="2" width="11" height="8" fill="none" stroke="#222"/><path d="M0.5 2l5.5 4.5L11.5 2" fill="none" stroke="#222"/></svg>
          Pale_Kettle@mailbox.example
        </li>
        <li>
          <svg viewBox="0 0 12 12" aria-hidden="true"><circle cx="6" cy="6" r="5.2" fill="none" stroke="#222"/><ellipse cx="6" cy="6" rx="2.2" ry="5.2" fill="none" stroke="#222"/><path d="M1 6h10" stroke="#222"/></svg>
          www.HollowThicket.example
        </li>
      </ul>
    </div>
  </section>

  <section class="card card--back">
    <div class="back__field"></div>
    <div class="back__photo" role="img" aria-label="Photo of a roaring grizzly bear head"></div>
    <div class="back__name">Hollow Thicket</div>
  </section>
</body>
</html>
```